Veldmark Supplies Business Card

Professional business card that stand out to our potential customers. Front and back with clean modern design

Industry/Entity Type

Oil and gas

Contact Information for Business Card

Name, address, website , office phone and cell number

Requirements
Must have
• Editable files for each employee

```html
<!DOCTYPE html>
<html lang="en">
<head>
<meta charset="utf-8">
<title>Veldmark Supplies Business Card</title>
<link rel="stylesheet" href="https://fonts.googleapis.com/css2?family=Jost:wght@400;500;600;700&display=swap">
<style>
  :root {
    --stage: #e4e5e7;
    --card: #ffffff;
    --card-shade: #f1f1f2;
    --brand-red: #e31e24;
    --brand-blue: #1aaccc;
    --ink: #3a3a3c;
    --ink-soft: #6d6e71;
    --rule: #f0a3a5;
  }
  * { box-sizing: border-box; margin: 0; padding: 0; }
  html, body {
    width: 1200px; height: 900px; overflow: hidden;
    background: var(--stage);
    font-family: "Jost", sans-serif;
  }
  .stage { position: relative; width: 1200px; height: 900px; }
  .card {
    position: absolute; left: 250px; width: 700px; height: 400px;
    overflow: hidden;
    background: linear-gradient(135deg, var(--card) 40%, var(--card-shade) 100%);
    box-shadow: 0 6px 18px rgba(0,0,0,0.18);
  }
  .card--front { top: 40px; }
  .card--back { top: 460px; }

  .wordmark {
    position: absolute; display: flex; align-items: center; gap: 12px;
    color: var(--brand-red); font-weight: 600; text-transform: uppercase;
    letter-spacing: 0.05em; white-space: nowrap; line-height: 1;
  }
  .wordmark__square { width: 0.9em; height: 0.9em; background: var(--brand-blue); flex: none; }
  .card--front .wordmark { right: 50px; top: 215px; font-size: 32px; }
  .card--back .wordmark { right: 50px; top: 140px; font-size: 22px; }

  .contact { position: absolute; left: 60px; top: 160px; color: var(--ink); }
  .contact__role { font-size: 14px; color: var(--ink-soft); line-height: 1; }
  .contact__name { font-size: 21px; font-weight: 700; text-transform: uppercase; line-height: 1.15; letter-spacing: 0.02em; }
  .contact__first { color: var(--brand-red); }
  .contact__last { color: var(--brand-blue); }
  .contact__list { list-style: none; margin-top: 4px; }
  .contact__list li {
    display: flex; align-items: center; gap: 10px;
    font-size: 15px; line-height: 24px; letter-spacing: 0.02em;
  }
  .contact__list li.gap { margin-top: 18px; }
  .contact__list svg { width: 14px; height: 14px; fill: none; stroke: var(--brand-red); stroke-width: 2; flex: none; }
  .contact__rule { width: 400px; height: 1px; background: var(--rule); margin: 10px 0 8px; }
  .contact__address { font-size: 17px; letter-spacing: 0.03em; color: var(--ink); line-height: 1.2; white-space: nowrap; }
</style>
</head>
<body>
<main class="stage">
  <section class="card card--front" aria-label="Card front">
    <div class="wordmark"><span class="wordmark__square"></span>Veldmark Supplies</div>
  </section>

  <section class="card card--back" aria-label="Card back">
    <div class="wordmark"><span class="wordmark__square"></span>Veldmark Supplies</div>

    <div class="contact">
      <p class="contact__role">Director</p>
      <p class="contact__name"><span class="contact__first">Dana</span> <span class="contact__last">Whitfield</span></p>
      <ul class="contact__list">
        <li>
          <svg viewBox="0 0 14 14" aria-hidden="true"><rect x="3" y="1" width="8" height="12" rx="1.5"/></svg>
          555-204-7183
        </li>
        <li class="gap">
          <svg viewBox="0 0 14 14" aria-hidden="true"><path d="M3 1.5l2.5 2.5-1.5 1.5a7 7 0 0 0 4.5 4.5l1.5-1.5 2.5 2.5-2 2A10 10 0 0 1 1 3.5z"/></svg>
          (555)318-0462
        </li>
        <li>
          <svg viewBox="0 0 14 14" aria-hidden="true"><rect x="1" y="3" width="12" height="8"/><path d="M1 3l6 5 6-5"/></svg>
          sales@veldmarksupplies.com
        </li>
        <li>
          <svg viewBox="0 0 14 14" aria-hidden="true"><circle cx="7" cy="7" r="6"/><path d="M1 7h12M7 1c-3 3-3 9 0 12M7 1c3 3 3 9 0 12"/></svg>
          www.veldmarksupplies.com
        </li>
      </ul>
      <div class="contact__rule"></div>
      <p class="contact__address">417 N.Harlow Lane Suite 5, Midland, Tx 79701</p>
    </div>
  </section>
</main>
</body>
</html>
```